Printing company needs stellar web site!

We need a website for a printing company based in Atlanta, Georgia, USA. Our company is 26 years old and just this year did a logo and branding refresh. Now we need our website to be refreshed as well.

Please see the attached source files for our new logo and stationary design.

Printing

```html
<!DOCTYPE html>
<html lang="en">
<head>
<meta charset="utf-8">
<title>Printvale – Printing Solutions</title>
<link rel="stylesheet" href="https://fonts.googleapis.com/css2?family=Lato:wght@400;700&family=Open+Sans:wght@400;600;700&family=Oswald:wght@500&display=swap">
<style>
:root{
  --brand:#1a6fc0;
  --brand-dark:#0b4f9a;
  --ink:#222;
  --text:#444;
  --muted:#777;
  --page:#f7f7f7;
  --band:#e6e6e6;
  --footer:#2b2b2b;
  --footer-bar:#1f1f1f;
  --cyan:#0bb8ea;
  --magenta:#e51d6c;
  --green:#77c423;
  --violet:#5a47b3;
}
*{margin:0;padding:0;box-sizing:border-box}
html,body{width:753px;height:1200px;overflow:hidden}
body{position:relative;background:#fff;font-family:'Lato',sans-serif;color:var(--text)}
.abs{position:absolute}

/* header */
.site-header{left:0;top:0;width:753px;height:105px;background:#fff}
.brand{left:0;width:753px;top:18px;text-align:center}
.brand-name{display:inline-flex;align-items:center;gap:8px;font-family:'Open Sans',sans-serif;font-weight:700;font-size:27px;letter-spacing:1px;color:var(--brand)}
.brand-dot{width:26px;height:26px;border-radius:50%;background:var(--brand)}
.tagline{font-family:'Lato',sans-serif;font-size:6.4px;color:var(--brand);letter-spacing:.2px;margin-top:1px;padding-left:30px}
.header-rule{left:165px;top:65px;width:423px;height:1px;background:#ddd}
.main-nav{top:78px;left:0;width:753px;display:flex;justify-content:center;gap:16px;font-family:'Open Sans',sans-serif;font-size:11.2px;color:#222}
.main-nav a{color:inherit;text-decoration:none;padding-bottom:4px}
.main-nav a.active{border-bottom:2px solid var(--brand)}

/* hero */
.hero{left:0;top:105px;width:753px;height:245px;background:linear-gradient(110deg,#ef3c86 0%,#f6a23a 22%,#e8e8e8 38%,#73c044 55%,#f05a9a 72%,#f2c230 86%,#16a39a 100%)}
.hero-caption{left:250px;top:286px;width:252px;height:64px;background:rgba(190,190,190,.8);color:#fff;font-family:'Oswald',sans-serif;font-size:21px;line-height:25px;text-align:center;padding-top:7px;letter-spacing:.3px}

/* experience */
.intro{left:0;top:350px;width:753px;height:348px;background:var(--page)}
.years{left:333px;top:369px;width:87px;height:26px;border-radius:13px;background:var(--brand);color:#fff;font-family:'Open Sans',sans-serif;font-size:17px;text-align:center;line-height:26px}
.years-tip{left:370px;top:394px}
.intro-title{left:0;width:753px;top:398px;text-align:center;font-family:'Open Sans',sans-serif;font-weight:600;color:#111}
.intro-title .big{display:block;font-size:32px;line-height:40px}
.intro-title .small{display:block;font-size:23px;line-height:22px}

.service{top:476px;width:126px;height:188px;color:#fff;text-align:center}
.service-title{height:38px;font-family:'Oswald',sans-serif;font-size:14px;line-height:16px;padding-top:4px;text-transform:uppercase}
.service-photo{position:absolute;left:-3px;top:39px;width:132px;height:75px;border:3px solid #fff}
.service-text{position:absolute;top:119px;left:6px;right:6px;font-size:7.6px;line-height:11.4px}
.service-btn{position:absolute;left:34px;top:161px;width:58px;height:19px;background:#fff;font-size:8px;line-height:19px}
.c-cyan{background:var(--cyan)}.c-cyan .service-btn{color:var(--cyan)}
.c-magenta{background:var(--magenta)}.c-magenta .service-btn{color:var(--magenta)}
.c-green{background:var(--green)}.c-green .service-btn{color:var(--green)}
.c-violet{background:var(--violet)}.c-violet .service-btn{color:var(--violet)}

/* specialty */
.specialty-band{left:0;top:698px;width:753px;height:219px;background:var(--band)}
.specialty-title{left:82px;top:720px;font-family:'Open Sans',sans-serif;font-size:16px;color:#222}
.specialty-copy{left:82px;top:748px;width:280px;font-size:8.2px;line-height:12.2px;color:#333}
.spec-list{list-style:none;font-size:8.2px;color:#333}
.spec-list li{height:17.6px;display:flex;align-items:center;gap:7px}
.spec-list li::before{content:"";width:7px;height:7px;border-radius:50%;background:var(--brand)}
.divider{left:387px;top:722px;width:1px;height:170px;background:#d4d4d4}

.tabs{left:418px;top:724px;display:flex;gap:2px}
.tab{height:27px;padding:0 15px;background:#ededed;border:1px solid #d8d8d8;font-size:7.6px;line-height:26px;color:#555;text-transform:uppercase}
.tab.active{background:#f7f7f7;border-bottom-color:#f7f7f7}
.news-panel{left:418px;top:750px;width:252px;height:135px;background:#f7f7f7;border:1px solid #dadada}
.news-photo{left:432px;top:778px;width:88px;height:88px;border:3px solid var(--brand);background:linear-gradient(135deg,#8fb9d6,#e7a64a 55%,#4a8fcf)}
.news-date{left:534px;top:778px;font-size:7px;color:var(--brand);font-weight:700}
.news-title{left:532px;top:788px;width:130px;font-family:'Open Sans',sans-serif;font-size:17px;line-height:21px;color:#222}
.news-body{left:532px;top:832px;width:125px;font-size:7.8px;line-height:11.2px;color:#666}

/* partners */
.partners{left:0;top:917px;width:753px;height:40px;display:flex;justify-content:center;gap:30px;align-items:center;font-family:'Lato',sans-serif;font-size:17px;color:#6a6a6a}
.partner{display:flex;align-items:center;gap:6px}
.partner-mark{width:14px;height:14px;border-radius:50%;background:#8a8a8a}

/* footer */
.footer{left:0;top:940px;width:753px;height:260px;background:var(--footer)}
.footer-curve{left:0;top:940px}
.foot-col{top:1052px;color:#ddd}
.foot-col h4{font-family:'Lato',sans-serif;font-weight:700;font-size:9.6px;color:#fff;padding-bottom:7px;border-bottom:1px solid #444;margin-bottom:8px}
.quick-links{list-style:none;font-size:7.4px}
.quick-links li{height:18.4px;display:flex;gap:6px;align-items:flex-start}
.quick-links li::before{content:"›";color:#ccc}
.contact-line{display:flex;gap:10px;align-items:center;font-size:7.4px;line-height:10px;margin-bottom:9px}
.contact-line.big{font-size:9.6px}
.contact-line svg{flex:none}
.map-box{width:127px;height:77px;border:2px solid #555;background:linear-gradient(135deg,#e9e2cf,#a9cfe8 60%,#d9d2bf)}
.news-note{font-size:7.4px;line-height:10.4px;margin-bottom:8px}
.email-field{width:127px;height:19px;background:#444;border-radius:2px;font-size:7.4px;font-style:italic;color:#bbb;line-height:19px;padding-left:7px;margin-bottom:12px}
.submit-btn{width:47px;height:15px;background:var(--brand);color:#fff;font-weight:700;font-size:8.4px;line-height:15px;text-align:center;border-radius:2px}
.footer-bar{left:0;top:1174px;width:753px;height:26px;background:var(--footer-bar)}
.copyright{left:83px;top:1183px;font-size:7.4px;color:#ddd}
.social{left:588px;top:1181px;display:flex;gap:9px}
.social span{width:12px;height:12px;border-radius:50%;background:#e6e6e6}
</style>
</head>
<body>

<header class="abs site-header">
  <div class="abs brand">
    <div class="brand-name"><span class="brand-dot"></span>PRINTVALE</div>
    <div class="tagline">OUTSTANDING SERVICE • QUALITY PRODUCT • COMPETITIVE PRICING.</div>
  </div>
  <div class="abs header-rule"></div>
  <nav class="abs main-nav">
    <a class="active">HOME</a><a>ABOUT US</a><a>OUR SERVICES</a><a>SUPPORT</a><a>BLOG</a><a>CONTACT</a>
  </nav>
</header>

<section class="abs hero" role="img" aria-label="Colourful overlapping ink circles artwork"></section>
<div class="abs hero-caption">ALL TYPES OF<br>PRINTING SOLUTIONS</div>

<section class="abs intro"></section>
<div class="abs years">26 years</div>
<svg class="abs years-tip" width="12" height="8" viewBox="0 0 12 8"><path d="M0 0H12L4 8Z" fill="var(--brand)"/></svg>
<h1 class="abs intro-title"><span class="big">OF PRINTING</span><span class="small">EXPERIENCE!</span></h1>

<article class="abs service c-cyan" style="left:86px">
  <div class="service-title">Envelope<br>Printing</div>
  <div class="service-photo" role="img" aria-label="Operator at a printing press control panel" style="background:linear-gradient(135deg,#d7dde4,#5a7fb8 60%,#e8e8e8)"></div>
  <p class="service-text">Lorem ipsum dolor sit amet, consectetur adipiscing elit. estibulum vitae vulputate risus.</p>
  <div class="service-btn">More</div>
</article>
<article class="abs service c-magenta" style="left:238px">
  <div class="service-title">Pad<br>Printing</div>
  <div class="service-photo" role="img" aria-label="Colour ink rollers on a press" style="background:linear-gradient(180deg,#555,#e84d8a 40%,#f2c12e 60%,#3a9be0 80%,#333)"></div>
  <p class="service-text">Lorem ipsum dolor sit amet, consectetur adipiscing elit. estibulum vitae vulputate risus.</p>
  <div class="service-btn">More</div>
</article>
<article class="abs service c-green" style="left:389px">
  <div class="service-title">Catalog<br>Printing</div>
  <div class="service-photo" role="img" aria-label="Printer ink cartridges" style="background:linear-gradient(135deg,#111,#3a3a3a 45%,#c3306a 60%,#1a1a1a)"></div>
  <p class="service-text">Lorem ipsum dolor sit amet, consectetur adipiscing elit. estibulum vitae vulputate risus.</p>
  <div class="service-btn">More</div>
</article>
<article class="abs service c-violet" style="left:540px">
  <div class="service-title">Real 3D<br>Printing</div>
  <div class="service-photo" role="img" aria-label="Large format print rolls" style="background:linear-gradient(180deg,#2a2a2a,#cfd6e2 35%,#b8283a 70%,#222)"></div>
  <p class="service-text">Lorem ipsum dolor sit amet, consectetur adipiscing elit. estibulum vitae vulputate risus.</p>
  <div class="service-btn">More</div>
</article>

<section class="abs specialty-band"></section>
<h2 class="abs specialty-title">Our Specialty</h2>
<p class="abs specialty-copy">Quisque magna orci, sagittis ac eros at, consectetur faucibus Pellentesque fermentum viverra commodo. Praesent fringilla et sem eu congue. Donec varius facilisis consequat. Suspendisse semper eu velit a adipisc Phasellus cursus, magna ac sagittis ultricies, ipsum quam gravida magna imperdiet erat ligula id leo. In a neque pretium, porta arcu eget, laoreet arcu.</p>
<ul class="abs spec-list" style="left:82px;top:821px">
  <li>Lorem ipsum dolor sit amet</li><li>Consectetuer adipiscing</li><li>Pt wisi enim ad</li><li>Aostrud exerci tation ullam</li>
</ul>
<ul class="abs spec-list" style="left:223px;top:821px">
  <li>Lorem ipsum dolor sit amet</li><li>Consectetuer adipiscing</li><li>Pt wisi enim ad</li><li>Aostrud exerci tation ullam</li>
</ul>
<div class="abs divider"></div>

<div class="abs news-panel"></div>
<div class="abs tabs"><div class="tab active">News</div><div class="tab">Tweets</div><div class="tab">Testimonials</div></div>
<div class="abs news-photo" role="img" aria-label="Hands choosing colour swatches"></div>
<div class="abs news-date">JUL 14</div>
<h3 class="abs news-title">Best Printing Ever!</h3>
<p class="abs news-body">Lorem ipsum dolor sit amet, consectetuer adipiscing elit, sed diam nonummy nibh</p>

<footer class="abs footer"></footer>
<svg class="abs footer-curve" width="753" height="110" viewBox="0 0 753 110">
  <path d="M0 0H753V16C650 52 520 96 380 98C250 100 80 92 0 8Z" fill="#fff"/>
  <path d="M0 8C80 92 250 100 380 98C520 96 650 52 753 16" fill="none" stroke="var(--brand-dark)" stroke-width="4"/>
  <path d="M0 14C90 98 260 106 390 103C530 100 660 58 753 24" fill="none" stroke="var(--brand)" stroke-width="1.5"/>
</svg>
<div class="abs partners">
  <div class="partner">Northbay</div>
  <div class="partner"><span class="partner-mark"></span>Lumawell</div>
  <div class="partner"><span class="partner-mark"></span>Fieldmark</div>
  <div class="partner"><span class="partner-mark"></span>Orbisco</div>
  <div class="partner"><span class="partner-mark"></span>KESTREL</div>
</div>

<div class="abs foot-col" style="left:82px;width:86px">
  <h4>Quick Links</h4>
  <ul class="quick-links"><li>Home</li><li>About Us</li><li>Our Services</li><li>Support</li><li>Contact</li></ul>
</div>
<div class="abs foot-col" style="left:206px;width:130px">
  <h4>Contact Us</h4>
  <div class="contact-line"><svg width="8" height="11" viewBox="0 0 8 11"><path d="M4 0A4 4 0 0 1 8 4C8 7 4 11 4 11S0 7 0 4A4 4 0 0 1 4 0Z" fill="#fff"/><circle cx="4" cy="4" r="1.5" fill="#2b2b2b"/></svg><span>123 PG Duis aute irure doloresg rephenderit in voluptate velit</span></div>
  <div class="contact-line big"><svg width="9" height="9" viewBox="0 0 9 9"><path d="M1 0L3 2 2 3.5Q3.5 5.5 5.5 7L7 6 9 8 8 9Q3 8 0 1Z" fill="#fff"/></svg><span>123 456 7890</span></div>
  <div class="contact-line big"><svg width="9" height="9" viewBox="0 0 9 9"><rect x="2" y="0" width="5" height="3" fill="#fff"/><rect x="0" y="3" width="9" height="4" fill="#fff"/><rect x="2" y="6" width="5" height="3" fill="#fff" stroke="#2b2b2b" stroke-width=".6"/></svg><span>123 456 7890</span></div>
  <div class="contact-line" style="font-weight:700"><svg width="10" height="7" viewBox="0 0 10 7"><rect width="10" height="7" fill="#fff"/><path d="M0 0L5 4 10 0" fill="none" stroke="#2b2b2b"/></svg><span>info@printvale.com</span></div>
</div>
<div class="abs foot-col" style="left:375px;width:127px">
  <h4 style="border:none;margin-bottom:4px">Location Map</h4>
  <div class="map-box" role="img" aria-label="Street map showing the office location"></div>
</div>
<div class="abs foot-col" style="left:543px;width:127px">
  <h4>Newsletter Sign Up</h4>
  <p class="news-note">Stay connected and receive email updates from sopedu</p>
  <div class="email-field">Enter Your Email</div>
  <div class="submit-btn">SUBMIT</div>
</div>

<div class="abs footer-bar"></div>
<p class="abs copyright">Copyright 2014 Printvale. All Rights Reserved.</p>
<div class="abs social" aria-label="Social links"><span></span><span></span><span></span><span></span></div>

</body>
</html>
```